Redesign of business card for Cedar Ridge Mechanical

We are looking for a new design for our business cards for Cedar Ridge Mechanical. We are a plumbing & HVAC construction company, operating on the West Coast of Canada and USA. Logo attached.
Industry/Entity Type
Construction - Plumbing & HVAC
Contact Information for Business Card
Name, address, phone numbers, email, website address
Look and feel
Each slider illustrates characteristics of the customer's brand and the style your logo design should communicate.

```html
<!DOCTYPE html>
<html lang="en">
<head>
<meta charset="utf-8">
<title>Cedar Ridge Mechanical – Business Card</title>
<link rel="stylesheet" href="https://fonts.googleapis.com/css2?family=Poppins:wght@400;700&display=swap">
<style>
  :root {
    --bg: #222222;
    --card-light: #e4e5e5;
    --card-dark: #1b1b1d;
    --ink: #0a0a0a;
    --emboss-light: #d6d7d7;
    --emboss-dark: #242427;
  }
  * { margin: 0; padding: 0; box-sizing: border-box; }
  html, body { width: 1200px; height: 780px; overflow: hidden; background: var(--bg); }
  body { font-family: "Poppins", sans-serif; position: relative; }

  .card {
    position: absolute;
    width: 540px;
    height: 310px;
    top: 235px;
    border-radius: 3px;
    overflow: hidden;
  }
  .card--front { left: 40px; background: var(--card-light); color: var(--ink); }
  .card--back { left: 620px; background: var(--card-dark); }

  .brand {
    position: absolute;
    display: flex;
    align-items: center;
    gap: 10px;
    font-weight: 700;
    text-transform: uppercase;
    letter-spacing: 0.04em;
  }
  .brand__mark { display: block; background: currentColor; }

  .card--front .brand { top: 34px; left: 34px; font-size: 15px; }
  .card--front .brand__mark { width: 14px; height: 14px; }

  .contact {
    position: absolute;
    top: 88px;
    left: 34px;
    font-size: 12.5px;
    line-height: 1.55;
    list-style: none;
  }
  .contact__address { margin-bottom: 4px; }
  .contact__item { display: flex; align-items: center; gap: 8px; }
  .contact__icon { width: 11px; height: 11px; flex: none; }

  .person {
    position: absolute;
    top: 92px;
    right: 34px;
    text-align: right;
  }
  .person__name { font-size: 30px; line-height: 1.1; font-weight: 400; }
  .person__name strong { font-weight: 700; }
  .person__role { font-size: 14px; margin-top: 4px; }

  .edge-tab {
    position: absolute;
    right: 0;
    top: 170px;
    width: 26px;
    height: 48px;
    background: var(--ink);
  }

  .card--front .brand--faint {
    left: 250px;
    top: 240px;
    font-size: 19px;
    color: var(--emboss-light);
  }

  .card--back .brand {
    inset: 0;
    justify-content: center;
    font-size: 26px;
    color: var(--emboss-dark);
  }
  .card--back .brand__mark { width: 22px; height: 22px; }
</style>
</head>
<body>

<section class="card card--front" aria-label="Business card front">
  <div class="brand"><span class="brand__mark"></span>Cedar Ridge Mechanical</div>

  <ul class="contact">
    <li class="contact__address">1840 Harbor Ln. Suite 310<br>Tacoma, WA 98402</li>
    <li class="contact__item">
      <svg class="contact__icon" viewBox="0 0 24 24" aria-hidden="true"><path fill="currentColor" d="M6.6 10.8a15 15 0 0 0 6.6 6.6l2.2-2.2a1 1 0 0 1 1-.25 11.4 11.4 0 0 0 3.6.57 1 1 0 0 1 1 1V20a1 1 0 0 1-1 1A17 17 0 0 1 3 4a1 1 0 0 1 1-1h3.5a1 1 0 0 1 1 1c0 1.25.2 2.45.57 3.57a1 1 0 0 1-.25 1z"/></svg>
      (253) 418-6027
    </li>
    <li class="contact__item">
      <svg class="contact__icon" viewBox="0 0 24 24" aria-hidden="true"><path fill="currentColor" d="M3 5h18a1 1 0 0 1 1 1v12a1 1 0 0 1-1 1H3a1 1 0 0 1-1-1V6a1 1 0 0 1 1-1zm9 7 8-5H4z"/></svg>
      info@cedarridgemech.com
    </li>
    <li class="contact__item">
      <svg class="contact__icon" viewBox="0 0 24 24" aria-hidden="true"><circle cx="12" cy="12" r="9" fill="none" stroke="currentColor" stroke-width="2"/><path d="M3 12h18M12 3c3 3 3 15 0 18M12 3c-3 3-3 15 0 18" fill="none" stroke="currentColor" stroke-width="1.6"/></svg>
      www.cedarridgemech.com
    </li>
  </ul>

  <div class="person">
    <p class="person__name"><strong>Marta</strong> Keller</p>
    <p class="person__role">Founder &amp; CEO</p>
  </div>

  <span class="edge-tab"></span>

  <div class="brand brand--faint">Cedar Ridge Mechanical</div>
</section>

<section class="card card--back" aria-label="Business card back">
  <div class="brand"><span class="brand__mark"></span>Cedar Ridge Mechanical</div>
</section>

</body>
</html>
```